Dietary supplement, Clean and simple.

Hi,
I’d like to talk about the project,

About us:
We are a dietary supplement (Vitamins, Minerals, amino acids etc.) company.
The goal is to have about 25 products at the end of this year. However, for this goal to be achieved we need a good label design to make our products represent our company values.
I’ll be here every day supporting your questions, we are fully committed to making the highest/best quality/customer experience possible.

About the design and our values:
- Professional (We are in the industry of professionalism and expertise. I would love to show we are competent at this, Id. Like to have the labels looks like we have done our research.)
- Efficient (White spacing, good use of the space available.)
- Simple (Straight forward, in 5 seconds they have to know what the product they have is/how functions. We’re trying to simplify it for the consumer.
- No distractions (the only visually “distracting” factor can be the vector art.)

The guidelines:
The goal is to have a universal design, with one element that changes (Vector art). I’ll attach a file/multiple files I think can show some visuals on what I’m looking for, and what parts of the design I think are good/bad.

Label size: 69x155mm (Front is 77.5mm)

Design whatever you think fits our image. You’re the design expert, all I care about is that it fits our company standards/image.

Use this color/font.
Font: Sans Serif
Main company color is Mind green #237D62 (Use this color for something in the design.)

What I thought would be cool/might looks ugly, who knows:
1. The front of the label: Should have 1 vector art, preferably in the top right corner. (That looks good in multiple colors. The vector can have multiple areas to color, I would prefer 2 main colors in the vector art. The interchangeable colors are used for multiple kinds of products.)
2. Text/product information on the left. The text that will have to be displayed:
- Product name for instance “Magnesium + B6”
- Description for the product for instance “Magnesium with ginger taste”
- Company name or logo. (Add ® behind it. We are soon to be trademark registered.)
3. We need to show the "daily intake" amount on the front and also the amount in the complete bottle. For instance, “Daily intake 1 capsule, 60 capsules”.
• You don’t have to design the backside of the label. After I chose a design, I’d like to chat and give specific information on what areas need to be assigned where. (Too complex because of the law.)
Updates

Hi, Please make the deadline 31 days total. I want designers to have the time to design. And not be rushed to finish it.

I want to extend the deadline because i feel like a slightly more medical look would be interesting. Hope you can come up with something!!

Target Market(s)

Dietary supplement consumers

Industry/Entity Type

Dietary supplements

Font styles to use
Sans Serif

Colors

Designer to choose colors to be used in the design.

Requirements
Must have
• Trademark icon "®" has to be at the top right after the company logo(text of logo)/name.

```html
<!DOCTYPE html>
<html lang="en">
<head>
<meta charset="UTF-8">
<title>Noble Calm Vitamin D3 Label</title>
<link href="https://fonts.googleapis.com/css2?family=IBM+Plex+Sans:wght@400;600;700&display=swap" rel="stylesheet">
<style>
  :root {
    --band-grey: #bcbdbf;
    --paper: #ffffff;
    --ink: #231f20;
    --mint-green: #237d62;
    --brand-green: #006b3b;
    --blue-top: #3b74ba;
    --blue-bottom: #2a2d70;
  }
  * { margin: 0; padding: 0; box-sizing: border-box; }
  html, body { width: 1200px; height: 1200px; overflow: hidden; }
  body {
    position: relative;
    background: var(--paper);
    font-family: "IBM Plex Sans", sans-serif;
    color: var(--ink);
  }
  .band { position: absolute; left: 0; width: 1200px; height: 66px; background: var(--band-grey); }
  .band--top { top: 0; }
  .band--bottom { bottom: 0; }

  .art-panel {
    position: absolute; left: 232px; top: 66px; width: 310px; height: 387px;
    background: linear-gradient(to bottom, var(--blue-top), var(--blue-bottom));
  }

  .brand-mark {
    position: absolute; left: 782px; top: 118px; width: 200px;
    text-align: center; color: var(--brand-green); font-weight: 700;
  }
  .brand-mark__dot {
    display: block; width: 34px; height: 34px; margin: 0 auto 10px;
    border-radius: 50%; background: var(--brand-green);
  }
  .brand-mark__name { font-size: 44px; line-height: 1; letter-spacing: 0.5px; }
  .brand-mark__sub { font-size: 16px; letter-spacing: 10px; margin-top: 8px; padding-left: 10px; }

  .company-name {
    position: absolute; left: 232px; top: 492px;
    font-size: 50px; font-weight: 400; line-height: 1; letter-spacing: 0.5px;
  }
  .company-name sup { font-size: 24px; vertical-align: 22px; margin-left: 6px; }

  .product-name {
    position: absolute; left: 230px; top: 556px;
    font-size: 94px; font-weight: 600; line-height: 1; letter-spacing: 1px;
  }
  .accent-rule {
    position: absolute; left: 232px; top: 700px; width: 310px; height: 9px;
    background: linear-gradient(to right, var(--blue-top), var(--blue-bottom));
  }
  .product-description {
    position: absolute; left: 232px; top: 731px;
    font-size: 48px; font-weight: 400; line-height: 1; letter-spacing: 0.5px;
  }

  .dotted-divider { position: absolute; left: 232px; top: 938px; }

  .capsule-icon {
    position: absolute; left: 231px; top: 979px; width: 40px; height: 78px;
    border: 2px solid var(--mint-green); border-radius: 20px;
  }
  .pack-count { position: absolute; left: 291px; top: 986px; line-height: 1; }
  .pack-count__number { font-size: 28px; font-weight: 600; color: var(--mint-green); }
  .pack-count__unit { font-size: 27px; font-weight: 400; margin-top: 6px; letter-spacing: 0.5px; }

  .daily-intake {
    position: absolute; right: 253px; top: 986px; text-align: right; line-height: 1;
  }
  .daily-intake__label { font-size: 27px; font-weight: 400; letter-spacing: 0.5px; }
  .daily-intake__value { font-size: 27px; font-weight: 600; color: var(--mint-green); margin-top: 6px; letter-spacing: 0.5px; }
  .daily-intake__rule {
    position: absolute; left: 966px; top: 980px; width: 3px; height: 76px; background: var(--mint-green);
  }
</style>
</head>
<body>
  <div class="band band--top"></div>

  <div class="art-panel" role="img" aria-label="Product vector art area in blue tones"></div>

  <div class="brand-mark">
    <span class="brand-mark__dot"></span>
    <div class="brand-mark__name">NOBLE</div>
    <div class="brand-mark__sub">CALM</div>
  </div>

  <div class="company-name">NOBLE CALM<sup>®</sup></div>
  <h1 class="product-name">Vitamin D3</h1>
  <div class="accent-rule"></div>
  <p class="product-description">Vitamin D3 2000iu</p>

  <svg class="dotted-divider" width="740" height="4" viewBox="0 0 740 4">
    <line x1="0" y1="2" x2="740" y2="2" stroke="#237d62" stroke-width="3" stroke-dasharray="8 13"/>
  </svg>

  <div class="capsule-icon"></div>
  <div class="pack-count">
    <div class="pack-count__number">60</div>
    <div class="pack-count__unit">SOFTGELS</div>
  </div>

  <div class="daily-intake">
    <div class="daily-intake__label">DAILY INTAKE</div>
    <div class="daily-intake__value">1 SOFTGEL</div>
  </div>
  <div class="daily-intake__rule"></div>

  <div class="band band--bottom"></div>
</body>
</html>
```